"Harbor Builders" is a residential building company and needs a new business card design and may re

We would like a redesign based on the existing logo, and would like to see a new font as well. We are bespoke home builders who build sustainable energy efficient homes.

Industry/Entity Type

Construction

Contact Information for Business Card

Business card size 40mm x 90mm

Colors

Designer to choose colors to be used in the design.

```html
<!DOCTYPE html>
<html lang="en">
<head>
<meta charset="utf-8">
<title>Harbor Builders – Business Card</title>
<link rel="stylesheet" href="https://fonts.googleapis.com/css2?family=Source+Sans+3:wght@400;600;700&family=PT+Sans+Narrow:wght@400;700&display=swap">
<style>
  :root {
    --backdrop: #8c8c8c;
    --card-light: #dddddf;
    --card-dark: #0a0a0b;
    --ink: #2b2b2b;
    --ink-soft: #4a4a4a;
    --rule: #9a9a9c;
    --leaf: #a3bd2a;
    --paper-text: #e4e4e6;
  }
  * { margin: 0; padding: 0; box-sizing: border-box; }
  html, body {
    width: 1105px; height: 1200px; overflow: hidden;
    background: var(--backdrop);
    font-family: "Source Sans 3", sans-serif;
  }
  .card {
    position: absolute; left: 182px; width: 747px; height: 427px;
  }
  .card--front { top: 119px; background: var(--card-light); color: var(--ink); }
  .card--back { top: 636px; background: var(--card-dark); }

  .wordmark {
    position: absolute; display: flex; align-items: center;
    font-weight: 700; line-height: 1; white-space: nowrap;
  }
  .wordmark__square { background: var(--leaf); flex: none; }
  .card--front .wordmark { left: 55px; top: 188px; font-size: 36px; color: var(--ink); gap: 14px; }
  .card--front .wordmark__square { width: 30px; height: 30px; }
  .card--back .wordmark { left: 0; right: 0; top: 180px; justify-content: center; font-size: 62px; color: var(--paper-text); gap: 24px; }
  .card--back .wordmark__square { width: 52px; height: 52px; }

  .divider {
    position: absolute; left: 372px; top: 112px; width: 2px; height: 208px;
    background: linear-gradient(var(--card-light), var(--rule) 20%, var(--rule) 80%, var(--card-light));
  }
  .details { position: absolute; left: 404px; top: 98px; }
  .details__name { font-size: 26px; font-weight: 700; color: var(--ink); }
  .details__company { margin-top: 10px; font-size: 16.5px; font-weight: 700; color: var(--ink-soft); }
  .details__address { font-size: 17px; color: var(--ink-soft); line-height: 22px; }
  .contact { list-style: none; margin-top: 14px; }
  .contact li {
    display: flex; align-items: center; gap: 12px;
    font-size: 17px; color: var(--ink-soft); line-height: 23.5px;
  }
  .contact svg { width: 14px; height: 14px; fill: var(--ink); flex: none; }
  .registration {
    margin-top: 14px; font-family: "PT Sans Narrow", sans-serif;
    font-size: 15px; color: var(--ink-soft);
  }
  .registration b { font-weight: 700; }
</style>
</head>
<body>
  <section class="card card--front">
    <div class="wordmark"><span class="wordmark__square"></span>Harbor Builders</div>
    <div class="divider"></div>
    <div class="details">
      <h1 class="details__name">Daniel Moretti</h1>
      <p class="details__company">Harbor Builders Pty Ltd</p>
      <p class="details__address">PO Box 2210 Westgate<br>LPO Riverside WA 6000</p>
      <ul class="contact">
        <li><svg viewBox="0 0 14 14" aria-hidden="true"><path d="M4 0h6a1 1 0 0 1 1 1v12a1 1 0 0 1-1 1H4a1 1 0 0 1-1-1V1a1 1 0 0 1 1-1zm.5 1.5v9h5v-9zM7 11.3a.8.8 0 1 0 0 1.6.8.8 0 0 0 0-1.6z"/></svg>0400 123 456</li>
        <li><svg viewBox="0 0 14 14" aria-hidden="true"><path d="M1 3h12v1L7 8 1 4zM1 5.3l6 4 6-4V11H1z"/></svg>daniel@harborbuilders.com.au</li>
        <li><svg viewBox="0 0 14 14" aria-hidden="true"><path d="M7 1a6 6 0 1 0 0 12A6 6 0 0 0 7 1zm-1 2.2 1.6 1-.6 1.6-1.8.4-1 1.6.6 1.8-1.2.8A4.6 4.6 0 0 1 6 2.5zm3 8.1-.4-1.5 1.3-1.2 1.2.3A4.6 4.6 0 0 1 9 11.3z"/></svg>www.harborbuilders.com.au</li>
      </ul>
      <p class="registration"><b>Registration:</b> 48391 &nbsp;<b>ABN:</b> 42 508 736 114</p>
    </div>
  </section>

  <section class="card card--back">
    <div class="wordmark"><span class="wordmark__square"></span>Harbor Builders</div>
  </section>
</body>
</html>
```